New web design for a service provider in the medical field

We are looking for a new design for our website. We are a company that repairs and sells medical endoscopes. Our customers include doctors and hospitals. Our current website can be found at https://lumavex.de/en/lumavex-english.
We need a new web design (without programming) for the following 3 pages:
-Startpage https://lumavex.de/en/lumavex-english/
-Used endoscopes https://lumavex.de/en/used-endoscopes/
-Purchase https://lumavex.de/en/purchase/
The design should be modern and stylish.
The blue color of the logo should be reflected on the page, but not too intrusive.
I have uploaded the images from the header. If more images are needed, let me know and I will upload them.

Target Market(s)
Doctors and hospitals

```html
<!DOCTYPE html>
<html lang="en">
<head>
<meta charset="utf-8">
<title>Lumavex – Web Design Pages</title>
<link href="https://fonts.googleapis.com/css2?family=Poppins:wght@300;400;500;600;700;800&display=swap" rel="stylesheet">
<style>
:root{
  --board:#dcdde0;
  --navy:#1b3f9b;
  --blue:#2f86d6;
  --sky:#3aa0e8;
  --red:#d81f26;
  --ink:#111418;
  --text:#3b3f46;
  --muted:#6b7079;
  --pale:#eceef2;
  --paleblue:#cfe1f3;
  --white:#ffffff;
  --black:#000000;
}
*{box-sizing:border-box;margin:0;padding:0}
html,body{width:946px;height:1200px;overflow:hidden;background:var(--board);font-family:'Poppins',sans-serif;color:var(--text)}
.board{position:absolute;left:0;top:0;width:1708px;height:2168px;transform:scale(0.55386);transform-origin:0 0}
.page{position:absolute;top:40px;width:506px;background:var(--white);overflow:hidden}
.abs{position:absolute}
.topbar{position:absolute;left:0;top:0;width:506px;height:38px;background:var(--white)}
.brand{position:absolute;left:46px;top:13px;display:flex;align-items:center;gap:4px;font-size:9px;font-weight:600;color:var(--navy)}
.brand i{width:7px;height:7px;border-radius:50%;background:var(--sky);display:block}
.tagline{position:absolute;left:159px;top:14px;font-size:7.5px;color:var(--ink)}
.pill-contact{position:absolute;top:10px;height:19px;border-radius:10px;background:var(--ink);color:var(--white);font-size:6.5px;display:flex;align-items:center;gap:4px;padding:0 8px}
.pill-contact svg{width:8px;height:8px}
.nav{position:absolute;left:0;top:38px;width:506px;height:26px;background:var(--navy);border-radius:10px 10px 0 0;display:flex;align-items:center;padding-left:44px;font-size:6.2px;color:var(--white);text-transform:uppercase}
.nav span{padding:0 6px;border-left:1px solid rgba(255,255,255,.7);line-height:8px}
.nav span:first-child{border-left:0;padding-left:0}
.hero-title{position:absolute;left:42px;font-size:21px;line-height:27px;font-weight:800;color:var(--ink);letter-spacing:.5px}
.eyebrow{font-size:10px;color:var(--ink)}
.h-sec{font-size:10.5px;font-weight:700;color:var(--ink);line-height:16px;letter-spacing:.3px}
.h-center{text-align:center;font-size:11px;font-weight:700;color:var(--ink);letter-spacing:.6px}
.h-blue{text-align:center;font-size:10.5px;font-weight:700;color:var(--sky);letter-spacing:.4px}
.p{font-size:6.4px;line-height:10.8px;color:var(--text)}
.btn{position:absolute;height:20px;border-radius:10px;background:var(--sky);color:var(--white);font-size:8px;display:flex;align-items:center;justify-content:center;box-shadow:0 2px 4px rgba(20,60,120,.25)}
.photo{position:absolute;overflow:hidden}
.round-l{border-radius:0 120px 120px 0;border-right:3px solid var(--blue)}
.round-r{border-radius:120px 0 0 120px;border-left:3px solid var(--blue)}
.tone-lab{background:linear-gradient(135deg,#e7edf3,#b9c7d6 55%,#8fa3b9)}
.tone-scope{background:linear-gradient(135deg,#f1f3f5,#9ba4ad 50%,#3a3f45)}
.tone-glove{background:linear-gradient(120deg,#e6f1f7,#8cc2e6 45%,#2d6fb8 70%,#cfe3f0)}
.tone-teal{background:linear-gradient(135deg,#d9eef4,#7fb9c9 50%,#2f6f86)}
.tone-device{background:linear-gradient(135deg,#f4f6f8,#c8ced6 45%,#d64a3a 60%,#4c5968)}
.tone-aqua{background:linear-gradient(135deg,#5fb7cf,#2b8ca8 55%,#1a4a5c)}
.bpill{position:absolute;height:22px;border-radius:11px;color:var(--white);font-size:8px;font-weight:500;display:flex;align-items:center;justify-content:center}
.b-navy{background:var(--navy)}.b-red{background:var(--red)}.b-black{background:var(--black)}
.card{position:absolute;width:130px;height:184px;overflow:hidden}
.card .ph{height:80px}
.card .body{height:104px;padding:8px 9px;color:var(--white)}
.card h4{font-size:10px;font-weight:600}
.card h5{font-size:7px;font-weight:600;margin:3px 0 4px}
.card p{font-size:6.4px;line-height:10px;opacity:.92}
.card .cbtn{display:inline-block;margin-top:7px;border:1px solid var(--white);border-radius:6px;font-size:6.4px;padding:2px 5px}
.feat{position:absolute;width:135px}
.feat .ic{position:absolute;left:0;top:0;width:20px;height:20px;border-radius:50%;background:var(--navy);display:flex;align-items:center;justify-content:center}
.feat .ic svg{width:11px;height:11px}
.feat h6{margin-left:28px;font-size:6.6px;font-weight:600;color:var(--ink)}
.feat p{margin-left:28px;font-size:5px;line-height:7.4px;color:var(--ink);font-weight:500;margin-top:2px}
.feat .more{margin-left:28px;margin-top:4px;font-size:5px;color:var(--muted)}
.feat .more b{color:var(--blue);font-weight:500;margin-left:14px}
.vline{position:absolute;width:0;border-left:1px dashed #9aa3ad}
.footer{position:absolute;left:0;width:506px;height:223px;background:var(--black);color:var(--white)}
.flogo{position:absolute;left:0;width:506px;top:58px;text-align:center;font-size:13px;font-weight:600;letter-spacing:.3px}
.flinks{position:absolute;left:0;width:506px;top:98px;text-align:center;font-size:6.6px}
.flinks span{margin:0 5px}
.fcontact{position:absolute;top:128px;left:70px;display:flex;align-items:center;font-size:6.4px;line-height:9.5px}
.fitem{display:flex;align-items:center;gap:12px;padding:0 12px;border-left:1px solid #555}
.fitem:first-child{border-left:0;padding-left:0}
.fico{width:24px;height:24px;border-radius:50%;background:var(--navy);display:flex;align-items:center;justify-content:center}
.fico svg{width:11px;height:11px}
.fline{position:absolute;left:48px;top:200px;width:410px;border-top:1px dashed #777}
.fcopy{position:absolute;left:0;width:506px;top:212px;text-align:center;font-size:6px}
.form{position:absolute;left:42px;top:618px;width:423px;height:371px;background:var(--pale);border-radius:8px}
.fl{position:absolute;font-size:7.6px;color:var(--ink)}
.fi{position:absolute;height:16px;background:var(--white);border:1px solid #dde0e5;font-size:5.8px;color:#9aa0a8;padding:4px 5px}
.fs{position:absolute;height:16px;background:var(--white);border:1px solid #dde0e5;font-size:6px;color:var(--ink);padding:4px 5px}
.fs::after{content:"⌄";position:absolute;right:5px;top:0;font-size:8px}
.fhead{position:absolute;left:0;width:423px;text-align:center;font-size:8px;color:var(--sky);font-weight:500}
</style>
</head>
<body>
<div class="board">

<!-- ============ START PAGE ============ -->
<section class="page" style="left:46px;height:1820px">
  <div class="topbar">
    <div class="brand"><i></i>Lumavex</div>
    <div class="tagline">Cause the outcome matters</div>
    <div class="pill-contact" style="left:276px"><svg viewBox="0 0 10 10"><rect x="1" y="2" width="8" height="6" fill="none" stroke="#fff"/><path d="M1 2l4 3 4-3" fill="none" stroke="#fff"/></svg>info@lumavex.de</div>
    <div class="pill-contact" style="left:380px"><svg viewBox="0 0 10 10"><path d="M2 1l2 2-1 1.5a6 6 0 0 0 2.5 2.5L7 6l2 2-1.5 1.5C4 9 1 6 .5 2.5z" fill="#fff"/></svg>+49 4100 555 210-0</div>
  </div>
  <nav class="nav"><span>Home</span><span>Endoscope Repair</span><span>Used Endoscopes</span><span>Endoscopy Systems</span><span>Endoscopy Accessories</span><span>Purchase</span></nav>

  <div class="abs" style="left:0;top:64px;width:506px;height:264px;background:linear-gradient(180deg,#f4f6f8,#e4e8ed)"></div>
  <div class="photo tone-lab" style="left:250px;top:64px;width:256px;height:240px;border-radius:0 0 0 150px;border-left:3px solid var(--blue);border-bottom:3px solid var(--blue)" role="img" aria-label="Doctor holding a flexible endoscope"></div>
  <h1 class="hero-title" style="top:130px">PUT YOUR<br>ENDOSCOPE IN<br>RELIABLE HANDS!</h1>
  <div class="btn" style="left:42px;top:225px;width:85px">Get Started</div>

  <div class="photo tone-lab" style="left:0;top:328px;width:246px;height:230px;border-radius:0 0 170px 0;border-right:3px solid var(--blue);border-bottom:3px solid var(--blue)" role="img" aria-label="Doctor examining a patient with an endoscope"></div>
  <div class="abs" style="left:274px;top:356px;width:200px">
    <div class="eyebrow">ABOUT US</div>
    <div class="h-sec" style="margin-top:3px">WE ARE YOUR EXPERTS FOR<br>REPAIRING FLEXIBLE ENDOSCOPES</div>
    <p class="p" style="margin-top:6px">Lumavex GmbH is specialized in repairing and sailing flexible endoscopes along with accessories and consumables. We offer endoscopes, processors, light sources, accessories and much more – with a focus on the manufacturers Oriva, Pexon and Fujara.</p>
    <p class="p" style="margin-top:10px">We applied for foundation in 2020, whereby Lumavex emerged from another company in the same business field. For this reason, all employees have many years of experience. Lumavex is a reliable contact for doctors and hospitals.</p>
  </div>
  <div class="btn" style="left:272px;top:540px;width:84px">Learn More</div>

  <div class="abs" style="left:0;top:612px;width:506px;height:290px;background:var(--pale)"></div>
  <div class="bpill b-navy" style="left:126px;top:640px;width:80px">ORIVA</div>
  <div class="bpill b-red" style="left:213px;top:640px;width:80px">PEXON</div>
  <div class="bpill b-black" style="left:300px;top:640px;width:80px">FUJARA</div>
  <div class="card" style="left:43px;top:678px">
    <div class="ph tone-scope" role="img" aria-label="Endoscope on a patient table"></div>
    <div class="body" style="background:var(--navy)"><h4>REPAIR</h4><h5>ENDOSCOPE REPAIR SERVICE</h5><p>Manufacturer-independent we repair and maintain endoscopes, individual components (e.g.</p><span class="cbtn">Repair request</span></div>
  </div>
  <div class="card" style="left:188px;top:678px">
    <div class="ph tone-glove" role="img" aria-label="Gloved hands handling endoscope parts"></div>
    <div class="body" style="background:var(--red)"><h4>SALE</h4><h5>USED ENDOSCOPES</h5><p>Our regular stock includes refurbished gastroscopes, coloscopes, bronchoscopes,</p><span class="cbtn">Purchase request</span></div>
  </div>
  <div class="card" style="left:333px;top:678px">
    <div class="ph tone-glove" role="img" aria-label="Endoscopy procedure in a clinic"></div>
    <div class="body" style="background:var(--black)"><h4>PURCHASE</h4><h5>USED ENDOSCOPES</h5><p>We are very interested in buying your old endoscopes – even defective and dismantled! We</p><span class="cbtn">Sell device</span></div>
  </div>

  <div class="photo tone-scope" style="left:258px;top:902px;width:248px;height:232px;border-radius:150px 0 0 150px;border-bottom:3px solid var(--blue)" role="img" aria-label="Endoscope control head close-up"></div>
  <div class="abs" style="left:42px;top:940px;width:200px">
    <div class="eyebrow">Endoscope</div>
    <div class="h-sec" style="margin-top:5px">ENDOSCOPE REPAIRS AND SECOND HAND ENDOSCOPES FROM LUMAVEX – CAUSE THE OUTCOME MATTERS!</div>
    <p class="p" style="margin-top:8px">Lumavex is a privileged partner for the start-up facility or optimisation of existing healthcare facilities, doctor's offices and hospitals. The quality and reliability of our products and our offered service are our best advertisement!</p>
  </div>
  <div class="btn" style="left:42px;top:1100px;width:84px">Learn More</div>

  <div class="abs" style="left:0;top:1170px;width:506px;height:140px;background:linear-gradient(100deg,#2a6ec2,#1c5fb3 60%,#2a78cc)"></div>
  <div class="abs" style="left:0;top:1196px;width:506px;text-align:center;color:#fff">
    <div style="font-size:10px;font-weight:600;letter-spacing:.5px">FAULTY ENDOSCOPE?</div>
    <div style="font-size:10px;margin-top:4px">We ensure quick and smooth repairs!</div>
    <div style="font-size:9px;font-weight:600;margin-top:5px;letter-spacing:.4px">SIMPLE PLACE A</div>
  </div>
  <div class="btn" style="left:211px;top:1262px;width:84px;background:#3e95e4">Pick-up order</div>

  <div class="h-center abs" style="left:0;top:1345px;width:506px">LUMAVEX GMBH, YOUR DECISION FOR YOUR FUTURE</div>
  <div class="abs" style="left:184px;top:1373px;width:138px;height:73px;background:var(--paleblue);border-radius:4px"></div>
  <div class="vline" style="left:59px;top:1396px;height:80px"></div>
  <div class="vline" style="left:202px;top:1400px;height:76px"></div>
  <div class="vline" style="left:344px;top:1396px;height:80px"></div>
  <div class="feat" style="left:49px;top:1381px"><div class="ic"><svg viewBox="0 0 12 12"><circle cx="6" cy="4" r="2.5" fill="none" stroke="#fff"/><path d="M2 11c0-3 8-3 8 0" fill="none" stroke="#fff"/></svg></div><h6>Fast repairs</h6><p>Keep potential disruptions in your doctor's office or in your hospital at minimum as a result of optimized processes and highly qualified specialists in our company</p><div class="more">Magna aliqua <b>Learn More →</b></div></div>
  <div class="feat" style="left:192px;top:1381px"><div class="ic" style="background:#fff;border:1px solid var(--navy)"><svg viewBox="0 0 12 12"><circle cx="6" cy="5" r="3" fill="none" stroke="#1b3f9b"/><path d="M4 8l-1 3 3-1 3 1-1-3" fill="none" stroke="#1b3f9b"/></svg></div><h6 style="color:#fff">On-site service</h6><p style="color:#fff">We will gladly pay you a visit to carry out analysis and repairs on site. Due to our many years of experience, it doesn't get any faster (subject to stock range).</p><div class="more" style="color:#fff">Magna aliqua <b style="color:#fff">Learn More →</b></div></div>
  <div class="feat" style="left:334px;top:1381px"><div class="ic"><svg viewBox="0 0 12 12"><path d="M2 2l8 8M3 9l2-2M7 3l2 2" stroke="#fff"/></svg></div><h6>Without a maintenance contract</h6><p>No subscription or other maintenance contract, but one-time and sustainable repair work</p><div class="more">Magna aliqua <b>Learn More →</b></div></div>
  <div class="feat" style="left:49px;top:1472px"><div class="ic"><svg viewBox="0 0 12 12"><circle cx="6" cy="6" r="4" fill="none" stroke="#fff"/><path d="M6 3v6M4.5 4.5h3" stroke="#fff"/></svg></div><h6>Highly cost efficient</h6><p>Benefit from our first class recommendations and implementation by our experienced staff. Our goals is to find the best solutions together with you at the</p><div class="more">Magna aliqua <b>Learn More →</b></div></div>
  <div class="feat" style="left:192px;top:1472px"><div class="ic"><svg viewBox="0 0 12 12"><rect x="2" y="3" width="8" height="6" fill="none" stroke="#fff"/><path d="M4 6h4" stroke="#fff"/></svg></div><h6>Loan equipment service</h6><p>Use our service of high-quality loan devices during the downtime of your defective endoscope (limited to stock)</p><div class="more">Magna aliqua <b>Learn More →</b></div></div>
  <div class="feat" style="left:334px;top:1472px"><div class="ic"><svg viewBox="0 0 12 12"><path d="M6 1l1.5 3 3.5.5-2.5 2.5.6 3.5L6 9l-3.1 1.5.6-3.5L1 4.5l3.5-.5z" fill="none" stroke="#fff"/></svg></div><h6>First class service</h6><p>Our clients always come first!</p><div class="more" style="margin-top:28px">Magna aliqua <b>Learn More →</b></div></div>
  <div class="btn" style="left:196px;top:1530px;width:114px;height:17px;font-size:6.4px">Learn more about Lumavex!</div>

  <footer class="footer" style="top:1597px">
    <div class="flogo">Lumavex</div>
    <div class="flinks"><span>INFORMATIONS</span><span>ABOUT US</span><span>CONTACT US</span><span>TOS</span><span>COPYRIGHTS</span><span>PRIVACY POLICY</span></div>
    <div class="fcontact">
      <div class="fitem"><div class="fico"><svg viewBox="0 0 12 12"><path d="M6 11S2 7 2 4.5a4 4 0 0 1 8 0C10 7 6 11 6 11z" fill="#fff"/><circle cx="6" cy="4.5" r="1.3" fill="#1b3f9b"/></svg></div><div>Talstraße 18<br>21400 Nordau<br>Germany</div></div>
      <div class="fitem"><div class="fico"><svg viewBox="0 0 10 10"><path d="M2 1l2 2-1 1.5a6 6 0 0 0 2.5 2.5L7 6l2 2-1.5 1.5C4 9 1 6 .5 2.5z" fill="#fff"/></svg></div><div>Phone<br>+49 4100 555 210-0</div></div>
      <div class="fitem"><div class="fico"><svg viewBox="0 0 10 10"><rect x="1" y="2" width="8" height="6" fill="none" stroke="#fff"/><path d="M1 2l4 3 4-3" fill="none" stroke="#fff"/></svg></div><div>info@lumavex.de</div></div>
    </div>
    <div class="fline"></div>
    <div class="fcopy">© Copyright 2022 Lumavex , All Rights Reserved.</div>
  </footer>
</section>

<!-- ============ USED ENDOSCOPES ============ -->
<section class="page" style="left:605px;height:2085px">
  <div class="topbar">
    <div class="brand"><i></i>Lumavex</div>
    <div class="tagline">Cause the outcome matters</div>
    <div class="pill-contact" style="left:276px"><svg viewBox="0 0 10 10"><rect x="1" y="2" width="8" height="6" fill="none" stroke="#fff"/><path d="M1 2l4 3 4-3" fill="none" stroke="#fff"/></svg>info@lumavex.de</div>
    <div class="pill-contact" style="left:380px"><svg viewBox="0 0 10 10"><path d="M2 1l2 2-1 1.5a6 6 0 0 0 2.5 2.5L7 6l2 2-1.5 1.5C4 9 1 6 .5 2.5z" fill="#fff"/></svg>+49 4100 555 210-0</div>
  </div>
  <nav class="nav"><span>Home</span><span>Endoscope Repair</span><span>Used Endoscopes</span><span>Endoscopy Systems</span><span>Endoscopy Accessories</span><span>Purchase</span></nav>
  <div class="photo tone-glove" style="left:0;top:64px;width:506px;height:220px" role="img" aria-label="Gloved hands holding an endoscope"></div>
  <h1 class="hero-title" style="top:162px">QUALITY WITHOUT<br>COMPROMISE</h1>

  <div class="abs" style="left:55px;top:314px;width:396px;text-align:center">
    <div class="eyebrow">Used Endoscopes</div>
    <div class="h-sec" style="margin-top:2px">PURCHASE OF USED ENDOSCOPES – THE<br>INEXPENSIVE ALTERNATIVE</div>
    <p class="p" style="margin-top:6px">Used endoscopes are an excellent, high-quality alternative to new equipment for all doctors and hospitals who want to add to their equipment pool cost-effectively. On our website you will find all types of equipment – gastroscopes, coloscopes, bronchoscopes, cystoscopes and duodenoscopes.</p>
    <p class="p" style="margin-top:6px">All used endoscopes that we offer for sale were already in medical use and have been professionally looked after and serviced during this time. In addition, we can offer you endoscopy accessories both for medical examinations and for cleaning and maintaining your endoscopes.</p>
    <div class="h-blue" style="margin-top:12px">QUALITY WITH WARRANTY FOR MORE SAFETY</div>
    <p class="p" style="margin-top:6px">After the purchase, our technicians subjected the devices to extensive technical tests and overhauled them. Last but not least, we rely on well-known brands that themselves stand for a high quality standard – Oriva, Pexon and Fujara. For these reasons we can offer a twelve month warranty on our used equipment!</p>
    <p class="p" style="margin-top:6px">Only tested quality leaves our company: To ensure the highest quality standards, we carry out an intensive outgoing inspection on every device before dispatch. We enclose documentation of the test result with your endoscope and archive it for future reference.</p>
    <div style="margin-top:22px;font-size:11px;font-weight:600;color:var(--ink)">How It Works</div>
  </div>
  <svg class="abs" style="left:90px;top:603px" width="40" height="44" viewBox="0 0 40 44"><circle cx="20" cy="18" r="15" fill="none" stroke="#111" stroke-width="1.5"/><circle cx="20" cy="18" r="10" fill="none" stroke="#111"/><path d="M20 12l2 4 4 .5-3 3 1 4-4-2-4 2 1-4-3-3 4-.5z" fill="none" stroke="#111"/><path d="M12 30l-3 10 5-2 3 4 2-8M28 30l3 10-5-2-3 4-2-8" fill="none" stroke="#111"/></svg>
  <div class="abs" style="left:220px;top:602px;width:60px;height:60px;border-radius:50%;background:var(--sky);border:2px solid var(--navy)"><svg width="60" height="60" viewBox="0 0 60 60"><circle cx="28" cy="30" r="8" fill="none" stroke="#fff" stroke-width="1.5"/><path d="M16 44c2-7 22-7 24 0" fill="none" stroke="#fff" stroke-width="1.5"/><rect x="34" y="16" width="12" height="8" rx="2" fill="none" stroke="#fff"/></svg></div>
  <svg class="abs" style="left:360px;top:608px" width="64" height="42" viewBox="0 0 64 42"><rect x="4" y="4" width="36" height="26" fill="none" stroke="#111" stroke-width="1.5"/><path d="M40 12h12l8 10v8H40z" fill="none" stroke="#111" stroke-width="1.5"/><circle cx="14" cy="33" r="4" fill="#fff" stroke="#111" stroke-width="1.5"/><circle cx="50" cy="33" r="4" fill="#fff" stroke="#111" stroke-width="1.5"/><path d="M15 16l5 5 9-9" fill="none" stroke="#111" stroke-width="1.5"/><path d="M0 14h8M0 20h6" stroke="#111"/></svg>
  <div class="abs" style="left:50px;top:672px;width:130px;text-align:center"><div style="font-size:7.4px;font-weight:600;color:var(--ink)">12 MONTHS WARRANTY</div><p class="p" style="font-size:5.6px;margin-top:3px">Highest quality standards</p></div>
  <div class="abs" style="left:186px;top:672px;width:130px;text-align:center"><div style="font-size:7.4px;font-weight:600;color:var(--sky)">BEST CUSTOMER SERVICE</div><p class="p" style="font-size:5.6px;margin-top:3px;line-height:8px">We are there for you - from 08:00 to 20:00!</p></div>
  <div class="abs" style="left:326px;top:672px;width:130px;text-align:center"><div style="font-size:7.4px;font-weight:600;color:var(--ink)">WORLDWIDE SHIPPING</div><p class="p" style="font-size:5.6px;margin-top:3px">Our service knows no borders!</p></div>

  <div class="abs" style="left:0;top:728px;width:506px;height:837px;background:var(--pale)"></div>
  <div class="h-center abs" style="left:0;top:763px;width:506px;font-size:12px">USED DEVICE – FAIR PRICE – FULL PERFORMANCE</div>

  <div class="photo tone-scope round-l" style="left:0;top:795px;width:250px;height:175px;border-bottom:3px solid var(--blue)" role="img" aria-label="Row of flexible video endoscopes hanging on a wall"></div>
  <div class="abs" style="left:274px;top:822px;width:190px"><div class="h-sec">FLEXIBLE VIDEO ENDOSCOPES</div><p class="p" style="margin-top:6px">Discover our flexible endoscopes from the best brands such as Oriva, Pexon and Fujara: gastroscopes, coloscopes, bronchoscopes, duodenoscopes, cystoscopes and more.</p></div>
  <div class="bpill b-navy" style="left:274px;top:902px;width:57px;height:16px;font-size:5.6px">ORIVA</div>
  <div class="bpill b-red" style="left:338px;top:902px;width:57px;height:16px;font-size:5.6px">PEXON</div>
  <div class="bpill b-black" style="left:401px;top:902px;width:57px;height:16px;font-size:5.6px">FUJARA</div>

  <div class="photo tone-device round-r" style="left:265px;top:983px;width:241px;height:175px;border-bottom:3px solid var(--blue)" role="img" aria-label="Endoscopy processor and light source front panel"></div>
  <div class="abs" style="left:42px;top:1021px;width:205px"><div class="h-sec">PROCESSORS AND LIGHT-SOURCES</div><p class="p" style="margin-top:6px">Provide better diagnosis to your patients by means of high-resolution imaging, implemented by the best video processors of the latest generation.</p></div>
  <div class="bpill b-navy" style="left:42px;top:1100px;width:57px;height:16px;font-size:5.6px">ORIVA</div>
  <div class="bpill b-red" style="left:106px;top:1100px;width:57px;height:16px;font-size:5.6px">PEXON</div>
  <div class="bpill b-black" style="left:169px;top:1100px;width:57px;height:16px;font-size:5.6px">FUJARA</div>

  <div class="photo tone-lab round-l" style="left:0;top:1165px;width:250px;height:175px;border-bottom:3px solid var(--blue)" role="img" aria-label="Clinician working at an endoscopy system tower"></div>
  <div class="abs" style="left:274px;top:1197px;width:190px"><div class="h-sec">ENDOSCOPY SYSTEMS</div><p class="p" style="margin-top:6px">We help you with configuring a complete endoscopy system for your needs and requirements - from the endoscope to the peripheral devices (processor, light source, screen, suction pump, etc.).</p></div>
  <div class="btn" style="left:274px;top:1277px;width:186px">Learn all about endoscopy-systems!</div>

  <div class="photo tone-aqua round-r" style="left:265px;top:1353px;width:241px;height:175px;border-bottom:3px solid var(--blue)" role="img" aria-label="Endoscopy accessories on a surgical drape"></div>
  <div class="abs" style="left:42px;top:1400px;width:205px"><div class="h-sec">ACCESORIES</div><p class="p" style="margin-top:6px">Cover your needs for consumables for single or multiple specific use – from biopsy forceps to cleaning brushes and much more.</p></div>
  <div class="btn" style="left:42px;top:1470px;width:156px">Find your accessories here!</div>

  <div class="h-blue abs" style="left:0;top:1587px;width:506px;font-size:11px">SECOND HAND ENDOSCOPES FROM LEADING MANUFACTURERS</div>
  <p class="p abs" style="left:90px;top:1604px;width:326px;text-align:center">Discover our range of second hand and refurbished endoscopes from leading manufacturers. We give a twelve month warranty for this.</p>
  <div class="bpill b-navy" style="left:126px;top:1646px;width:80px">ORIVA</div>
  <div class="bpill b-red" style="left:213px;top:1646px;width:80px">PEXON</div>
  <div class="bpill b-black" style="left:300px;top:1646px;width:80px">FUJARA</div>
  <div class="h-center abs" style="left:0;top:1689px;width:506px;line-height:12px;font-size:10px">WE ARE YOUR FIRST CHOICE WHEN BUYING<br>USED ENDOSCOPY EQUIPMENT</div>
  <div class="vline" style="left:95px;top:1752px;height:50px"></div>
  <div class="vline" style="left:273px;top:1752px;height:50px"></div>
  <div class="feat" style="left:85px;top:1732px;width:165px"><div class="ic"><svg viewBox="0 0 12 12"><rect x="2" y="2" width="8" height="8" fill="none" stroke="#fff"/><path d="M4 6l1.5 1.5L8 4.5" fill="none" stroke="#fff"/></svg></div><h6>As new equipment</h6><p>The devices have already been in medical use before but were professionally maintained and serviced. Consumable parts were completely renewed after purchase by Lumavex GmbH.</p></div>
  <div class="feat" style="left:263px;top:1732px;width:165px"><div class="ic"><svg viewBox="0 0 12 12"><rect x="2" y="3" width="8" height="6" fill="none" stroke="#fff"/><path d="M2 5h8" stroke="#fff"/></svg></div><h6>Brand manufacturers</h6><p>We primarily offer the brands Oriva, Pexon and Fujara, which are characterized by long-lasting quality and whose manufacturers have already earned a good reputation as a result.</p></div>
  <div class="feat" style="left:85px;top:1805px;width:165px"><div class="ic"><svg viewBox="0 0 12 12"><circle cx="6" cy="6" r="4" fill="none" stroke="#fff"/><path d="M4 6l1.5 1.5L8 4.5" fill="none" stroke="#fff"/></svg></div><h6>Tested and overhauled</h6><p>Our trained technicians have checked and overhauled every device in a variety of ways before it is offered for resale.</p></div>
  <div class="feat" style="left:263px;top:1805px;width:165px"><div class="ic"><svg viewBox="0 0 12 12"><path d="M3 5h6l-2-2M9 7H3l2 2" fill="none" stroke="#fff"/></svg></div><h6>Trade-in of old devices</h6><p>As an additional service, if you wish, we will trade in your old device. After an assessment, we will easily offset the residual value with your new device.</p></div>

  <footer class="footer" style="top:1862px">
    <div class="flogo">Lumavex</div>
    <div class="flinks"><span>INFORMATIONS</span><span>ABOUT US</span><span>CONTACT US</span><span>TOS</span><span>COPYRIGHTS</span><span>PRIVACY POLICY</span></div>
    <div class="fcontact">
      <div class="fitem"><div class="fico"><svg viewBox="0 0 12 12"><path d="M6 11S2 7 2 4.5a4 4 0 0 1 8 0C10 7 6 11 6 11z" fill="#fff"/><circle cx="6" cy="4.5" r="1.3" fill="#1b3f9b"/></svg></div><div>Talstraße 18<br>21400 Nordau<br>Germany</div></div>
      <div class="fitem"><div class="fico"><svg viewBox="0 0 10 10"><path d="M2 1l2 2-1 1.5a6 6 0 0 0 2.5 2.5L7 6l2 2-1.5 1.5C4 9 1 6 .5 2.5z" fill="#fff"/></svg></div><div>Phone<br>+49 4100 555 210-0</div></div>
      <div class="fitem"><div class="fico"><svg viewBox="0 0 10 10"><rect x="1" y="2" width="8" height="6" fill="none" stroke="#fff"/><path d="M1 2l4 3 4-3" fill="none" stroke="#fff"/></svg></div><div>info@lumavex.de</div></div>
    </div>
    <div class="fline"></div>
    <div class="fcopy">© Copyright 2022 Lumavex , All Rights Reserved.</div>
  </footer>
</section>

<!-- ============ PURCHASE ============ -->
<section class="page" style="left:1147px;height:1250px">
  <div class="topbar">
    <div class="brand"><i></i>Lumavex</div>
    <div class="tagline">Cause the outcome matters</div>
    <div class="pill-contact" style="left:276px"><svg viewBox="0 0 10 10"><rect x="1" y="2" width="8" height="6" fill="none" stroke="#fff"/><path d="M1 2l4 3 4-3" fill="none" stroke="#fff"/></svg>info@lumavex.de</div>
    <div class="pill-contact" style="left:380px"><svg viewBox="0 0 10 10"><path d="M2 1l2 2-1 1.5a6 6 0 0 0 2.5 2.5L7 6l2 2-1.5 1.5C4 9 1 6 .5 2.5z" fill="#fff"/></svg>+49 4100 555 210-0</div>
  </div>
  <nav class="nav"><span>Home</span><span>Endoscope Repair</span><span>Used Endoscopes</span><span>Endoscopy Systems</span><span>Endoscopy Accessories</span><span>Purchase</span></nav>
  <div class="photo tone-teal" style="left:0;top:64px;width:506px;height:220px" role="img" aria-label="Gloved hands holding an endoscope control head"></div>
  <h1 class="hero-title" style="top:144px">SUSTAINABLE AND<br>ECONOMICAL</h1>

  <div class="abs" style="left:0;top:284px;width:506px;height:234px;background:var(--pale)"></div>
  <div class="photo tone-scope round-l" style="left:0;top:310px;width:250px;height:174px;border-bottom:3px solid var(--blue)" role="img" aria-label="Close-up of an endoscope control section"></div>
  <div class="abs" style="left:270px;top:334px;width:210px"><div class="h-sec">DO YOU WANT TO SELL YOUR ENDOSCOPE? YOU ARE AT THE RIGHT</div><p class="p" style="margin-top:5px">We are always interested in buying used endoscopes, accessories and peripherals from Oriva, Pexon and Fujara at fair conditions. We can promise you an objective offer with a clear conscience! Use the form below to offer us your device! If you want to have several devices checked, one of our technicians will usually come to you for the check. We also check defective and incomplete devices!</p></div>

  <div class="h-center abs" style="left:0;top:545px;width:506px;font-size:11.5px">ARE YOU LOOKING TO REPLACE YOUR FOR SALE DEVICE?</div>
  <div class="btn" style="left:138px;top:572px;width:230px">Browse our range of excellent used equipment!</div>

  <div class="form">
    <div class="fhead" style="top:15px">PERSONAL INFORMATIONS</div>
    <div class="fl" style="left:14px;top:38px">Salutation</div><div class="fs" style="left:94px;top:36px;width:124px">Choose</div>
    <div class="fl" style="left:236px;top:38px">co. / dr. off</div><div class="fi" style="left:298px;top:36px;width:114px;color:var(--ink)">Company / doctor's office</div>
    <div class="fl" style="left:14px;top:60px">Surname</div><div class="fi" style="left:94px;top:58px;width:124px">Surname</div>
    <div class="fl" style="left:236px;top:60px">Firstname</div><div class="fi" style="left:298px;top:58px;width:114px">Firstname</div>
    <div class="fl" style="left:14px;top:82px">Email</div><div class="fi" style="left:94px;top:80px;width:124px">Email</div>
    <div class="fl" style="left:236px;top:82px">Telephone</div><div class="fi" style="left:298px;top:80px;width:114px">Telephone</div>
    <div class="fhead" style="top:117px">INFORMATIONS ABOUT THE DEVICE</div>
    <div class="fl" style="left:14px;top:143px">Brand</div><div class="fs" style="left:94px;top:141px;width:124px">Choose</div>
    <div class="fl" style="left:236px;top:143px">Model</div><div class="fs" style="left:298px;top:141px;width:114px">Choose</div>
    <div class="fl" style="left:14px;top:165px">Defects / damage</div><div class="fi" style="left:94px;top:163px;width:124px">Surname</div>
    <div class="fl" style="left:236px;top:165px">Asking price</div><div class="fi" style="left:298px;top:163px;width:114px">Asking price</div>
    <div class="fhead" style="top:198px;text-align:left;left:14px;width:auto">REMARKS AND PICTURE</div>
    <div class="fl" style="left:14px;top:221px">Brand</div><div class="fi" style="left:58px;top:219px;width:172px;height:48px;color:var(--ink)">Brief description of the error other information etc.</div>
    <div class="fl" style="left:238px;top:221px">Upload picture</div><div class="fi" style="left:300px;top:219px;width:50px">Choose File</div>
    <div class="abs" style="left:358px;top:223px;font-size:5.8px;color:#9aa0a8">No file Chosen</div>
    <div class="abs" style="left:12px;top:292px;width:400px;font-size:5.8px;line-height:10px;color:var(--ink);text-align:center">☑ I have read the privacy policy and accept it. I agree above input will be transmitted to Lumavex GmbH to get in contact with me respectively to process my request and store all needed informations. Neither a transfer to third parties will happen, nor a use for advertising purposes by Lumavex GmbH!</div>
    <div class="btn" style="left:169px;top:337px;width:85px">Send Now</div>
  </div>

  <footer class="footer" style="top:1027px">
    <div class="flogo">Lumavex</div>
    <div class="flinks"><span>INFORMATIONS</span><span>ABOUT US</span><span>CONTACT US</span><span>TOS</span><span>COPYRIGHTS</span><span>PRIVACY POLICY</span></div>
    <div class="fcontact">
      <div class="fitem"><div class="fico"><svg viewBox="0 0 12 12"><path d="M6 11S2 7 2 4.5a4 4 0 0 1 8 0C10 7 6 11 6 11z" fill="#fff"/><circle cx="6" cy="4.5" r="1.3" fill="#1b3f9b"/></svg></div><div>Talstraße 18<br>21400 Nordau<br>Germany</div></div>
      <div class="fitem"><div class="fico"><svg viewBox="0 0 10 10"><path d="M2 1l2 2-1 1.5a6 6 0 0 0 2.5 2.5L7 6l2 2-1.5 1.5C4 9 1 6 .5 2.5z" fill="#fff"/></svg></div><div>Phone<br>+49 4100 555 210-0</div></div>
      <div class="fitem"><div class="fico"><svg viewBox="0 0 10 10"><rect x="1" y="2" width="8" height="6" fill="none" stroke="#fff"/><path d="M1 2l4 3 4-3" fill="none" stroke="#fff"/></svg></div><div>info@lumavex.de</div></div>
    </div>
    <div class="fline"></div>
    <div class="fcopy">© Copyright 2022 Lumavex , All Rights Reserved.</div>
  </footer>
</section>

</div>
</body>
</html>
```